Simplified minimalist but bold website

Design a website for a brand 'Brighten Every Day' that shares ideas to make managing home and health easier through email swap series, webinars and eventually courses.

Simple landing page to attract users to sign up for a freebie.

Target Market(s)

women with families & homes to run

Number of Pages Required

1 page

Font styles to use
Sans Serif

Colors
e667a6
b768aa
acd136
ffffff
959595

Requirements
Must have
• Simplified look, line icons, opt-in template, contact us form

```html
<!DOCTYPE html>
<html lang="en">
<head>
<meta charset="utf-8">
<title>Brighten Every Day</title>
<link href="https://fonts.googleapis.com/css2?family=Lato:wght@300;400;700;900&display=swap" rel="stylesheet">
<style>
:root{
  --pink:#e667a6;
  --purple:#b768aa;
  --green:#acd136;
  --blue:#3fa6dd;
  --white:#ffffff;
  --grey:#959595;
  --heading:#3c3c3c;
}
*{box-sizing:border-box;margin:0;padding:0}
html,body{width:786px;height:1200px;overflow:hidden;background:var(--white)}
body{font-family:'Lato',sans-serif;color:var(--white)}
.page{width:786px;height:1200px;position:relative}

/* Hero */
.hero{position:relative;height:367px;overflow:hidden;text-align:center}
.hero-photo{position:absolute;inset:0;background:linear-gradient(180deg,#3a3a3d 0%,#55514d 45%,#6e675f 75%,#4a4541 100%)}
.hero-shade{position:absolute;inset:0;background:rgba(20,20,22,.35)}
.hero-content{position:relative;z-index:1}
.brand-title{padding-top:24px;font-size:24px;font-weight:700;letter-spacing:1.5px;color:var(--pink);text-transform:uppercase}
.tagline{margin-top:194px;font-size:17px;font-weight:400;letter-spacing:.4px;line-height:1.5;text-transform:uppercase}
.scroll-mouse{display:block;margin:14px auto 0}

/* Offers */
.offers{display:flex;height:393px}
.offer{flex:1;display:flex;flex-direction:column;padding:30px 36px 42px;text-align:center}
.offer--swaps{background:var(--green)}
.offer--guide{background:var(--blue)}
.offer-kicker{font-size:10px;font-style:italic;font-weight:300;margin-bottom:8px}
.offer-title{font-size:20px;font-weight:700;margin-bottom:14px}
.offer-text{font-size:9px;line-height:1.6;padding:0 40px}
.offer-links{display:flex;justify-content:center;gap:28px;margin-top:16px}
.offer-link{font-size:8.5px;font-weight:700;text-transform:uppercase;color:var(--white);text-decoration:none;display:flex;align-items:center;gap:4px}
.signup{margin-top:auto}
.divider{border:0;border-top:1px solid rgba(255,255,255,.6);margin:0 30px 14px}
.form-label{font-size:10px;font-style:italic;font-weight:300;margin-bottom:14px}
.opt-in{display:flex;flex-direction:column;align-items:center;gap:8px}
.field{width:240px;height:22px;border:1px solid rgba(255,255,255,.85);background:transparent;color:var(--white);font-family:inherit;font-size:9px;text-align:center}
.field::placeholder{color:var(--white)}
.btn{background:var(--pink);color:var(--white);border:0;font-family:inherit;font-size:9px;font-weight:700;text-transform:uppercase;padding:6px 0;width:118px;margin-top:6px}
.guide-cover{display:block;width:152px;height:110px;margin:12px auto 0;background:var(--white);padding:6px;border:1px solid rgba(0,0,0,.08)}
.guide-cover-fill{width:100%;height:100%;background:linear-gradient(135deg,#f0a35e 0%,#e0795a 40%,#6fa9c9 100%)}

/* Details */
.details{height:304px;padding:98px 110px 0;text-align:center;color:var(--grey)}
.details-title{font-size:23px;font-weight:700;color:var(--heading);margin-bottom:22px}
.details-text{font-size:8.5px;line-height:1.7;margin-bottom:16px}
.details .btn{margin-top:18px;width:150px}

/* Footer */
.site-footer{height:136px;background:linear-gradient(135deg,var(--purple) 0%,#a35aa0 100%);text-align:center;padding-top:14px}
.social{display:flex;justify-content:center;gap:10px;margin-bottom:16px}
.social-dot{width:30px;height:30px;border:2px solid rgba(255,255,255,.9);border-radius:50%}
.footer-nav{display:flex;justify-content:center;font-size:9px}
.footer-nav a{color:var(--white);text-decoration:none;padding:0 15px;border-right:1px solid rgba(255,255,255,.6)}
.footer-nav a:last-child{border-right:0}
.copyright{font-size:8.5px;margin-top:12px}
</style>
</head>
<body>
<div class="page">

  <header class="hero">
    <div class="hero-photo" role="img" aria-label="Bright modern living room interior with sofa, plants and framed prints"></div>
    <div class="hero-shade"></div>
    <div class="hero-content">
      <h1 class="brand-title">Brighten Every Day</h1>
      <p class="tagline">Chances are life is a little overwhelming.<br>Let us help</p>
      <svg class="scroll-mouse" width="16" height="28" viewBox="0 0 18 30" aria-hidden="true">
        <rect x="1.5" y="1.5" width="15" height="24" rx="7.5" fill="none" stroke="#fff" stroke-width="2"/>
        <line x1="9" y1="6" x2="9" y2="11" stroke="#fff" stroke-width="2" stroke-linecap="round"/>
        <line x1="9" y1="27" x2="9" y2="30" stroke="#fff" stroke-width="1.5"/>
      </svg>
    </div>
  </header>

  <section class="offers">
    <article class="offer offer--swaps">
      <p class="offer-kicker">Baby Steps... (try out a few of our tricks)</p>
      <h2 class="offer-title">Swaps Email Series</h2>
      <p class="offer-text">Save TIME, MONEY and SANITY with simple product swaps. Reduce the amount of work it takes to run your home. Swap out existing products for more sustainable ones. Each swap saves you time, every week.</p>
      <div class="offer-links">
        <a class="offer-link" href="#">See sample swap
          <svg width="9" height="9" viewBox="0 0 10 10" aria-hidden="true"><circle cx="5" cy="5" r="4.3" fill="none" stroke="#fff"/><path d="M4 3l2 2-2 2" fill="none" stroke="#fff"/></svg></a>
        <a class="offer-link" href="#">Learn more
          <svg width="9" height="9" viewBox="0 0 10 10" aria-hidden="true"><circle cx="5" cy="5" r="4.3" fill="none" stroke="#fff"/><path d="M4 3l2 2-2 2" fill="none" stroke="#fff"/></svg></a>
      </div>
      <div class="signup">
        <hr class="divider">
        <p class="form-label">Send your details this way</p>
        <form class="opt-in">
          <input class="field" type="text" placeholder="Name">
          <input class="field" type="email" placeholder="Email">
          <button class="btn" type="button">Send me the swaps</button>
        </form>
      </div>
    </article>

    <article class="offer offer--guide">
      <p class="offer-kicker">Big Leap... (I'm ready to roll up my sleeves)</p>
      <h2 class="offer-title">Decluttering Guide</h2>
      <div class="guide-cover"><div class="guide-cover-fill" role="img" aria-label="Cover of the decluttering guide with tidy home photos"></div></div>
      <div class="signup">
        <form class="opt-in">
          <input class="field" type="text" placeholder="Name">
          <input class="field" type="email" placeholder="Email">
          <button class="btn" type="button">Sign me up</button>
        </form>
      </div>
    </article>
  </section>

  <section class="details">
    <h2 class="details-title">Swaps Email Series</h2>
    <p class="details-text">Save TIME, MONEY and SANITY with simple product swaps, and reduce the amount of work it takes to run your home. Swap out existing products for more sustainable ones. Each swap saves you time, money and stress.</p>
    <p class="details-text">You get an email for 6-12 weeks with one swap each week. If you find them helpful, join our monthly HAPPY HOME SWAP CIRCLE and share your own swaps with other mums.</p>
    <button class="btn" type="button">Sign me up</button>
  </section>

  <footer class="site-footer">
    <div class="social" aria-label="Social links">
      <span class="social-dot"></span><span class="social-dot"></span><span class="social-dot"></span><span class="social-dot"></span><span class="social-dot"></span>
    </div>
    <nav class="footer-nav">
      <a href="#">Home</a><a href="#">About Us</a><a href="#">Our Services</a><a href="#">Our Tools</a><a href="#">Contact</a><a href="#">Projects</a><a href="#">FAQs</a>
    </nav>
    <p class="copyright">Copyright © 2018 Brighten Every Day. All Rights Reserved &nbsp;|&nbsp; Privacy Policy</p>
  </footer>

</div>
</body>
</html>
```